Roofing company in Toronto, Canada needs a logo design and business card design

We need a business card and logo created for our company. Our company is "KLV Roofing" which provides roofing services for commercial and residential customers. We serve customers in the Greater Toronto Area (in Canada) thus the name KLV.

We want the logo and business card to be a modern design displaying professionalism and quality in the work. We would prefer rounded corners for the business cards but are open to other ideas. The cards should be pleasant and appealing to customers.

Target Market(s)

Commercial and Residential customers

Industry/Entity Type

Roofing

Contact Information for Business Card

Logo Text

KLV Roofing

Requirements
Nice to have
• Colours that are pleasing to the eye but at the same time should stand out from other business cards. If the design can incorporate the name of KLV Roofing and the actual concept of roofing that would be nice.
Should not have
• Do not want the business cards or logo to be childish looking. Need to look professionally designed.

```html
<!DOCTYPE html>
<html lang="en">
<head>
<meta charset="utf-8">
<title>KLV Roofing – Business Card</title>
<link rel="stylesheet" href="https://fonts.googleapis.com/css2?family=Tinos:wght@400;700&display=swap">
<style>
  :root {
    --stage: #3a3431;
    --card-dark: #0b0b0b;
    --card-light: #ffffff;
    --ink: #151515;
    --ink-soft: #2a2a2a;
    --accent: #e4202a;
    --paper-text: #f2f2f2;
    --ghost-dark: rgba(255,255,255,0.06);
    --ghost-light: rgba(0,0,0,0.05);
  }
  * { box-sizing: border-box; margin: 0; padding: 0; }
  html, body {
    width: 1200px; height: 780px; overflow: hidden;
    background: var(--stage);
    font-family: "Tinos", "Times New Roman", serif;
  }
  .canvas {
    position: relative; width: 1200px; height: 780px;
    display: flex; align-items: center; justify-content: center; gap: 60px;
  }
  .card {
    position: relative; width: 510px; height: 292px;
    border-radius: 14px; overflow: hidden;
    box-shadow: 0 14px 30px rgba(0,0,0,0.45);
  }
  /* Front */
  .card-front { background: var(--card-dark); display: flex; align-items: center; justify-content: center; }
  .card-front .ghost-name {
    position: absolute; left: 40px; bottom: 30px;
    font-size: 54px; color: var(--ghost-dark); letter-spacing: 3px;
  }
  .brand { display: flex; align-items: center; gap: 14px; position: relative; }
  .brand-dot { width: 22px; height: 22px; border-radius: 50%; background: var(--accent); }
  .brand-name { font-size: 34px; font-weight: 700; letter-spacing: 2px; color: var(--paper-text); }

  /* Back */
  .card-back { background: var(--card-light); color: var(--ink); }
  .card-back .ghost-name {
    position: absolute; left: 120px; top: 130px;
    font-size: 58px; color: var(--ghost-light); letter-spacing: 3px;
  }
  .person { position: absolute; left: 32px; top: 28px; }
  .person-name { font-size: 21px; font-weight: 700; letter-spacing: 1px; }
  .person-role { font-size: 15px; color: var(--accent); margin-top: -2px; }
  .company { position: absolute; left: 32px; top: 112px; font-size: 20px; }
  .rule-main { position: absolute; left: 32px; right: 32px; top: 142px; height: 1px; background: var(--ink); }
  .contacts { position: absolute; left: 32px; top: 156px; list-style: none; }
  .contacts li { display: flex; align-items: center; gap: 8px; font-size: 15px; line-height: 22px; color: var(--ink-soft); }
  .contacts svg { width: 15px; height: 15px; flex: none; }
  .card-back .brand { position: absolute; right: 30px; top: 168px; gap: 8px; }
  .card-back .brand-dot { width: 14px; height: 14px; }
  .card-back .brand-name { font-size: 22px; color: var(--ink); letter-spacing: 1px; }
  .rule-address { position: absolute; right: 32px; top: 226px; width: 210px; height: 1px; background: var(--ink); }
  .address { position: absolute; right: 32px; top: 234px; text-align: right; font-size: 15px; line-height: 19px; }
</style>
</head>
<body>
<main class="canvas">
  <section class="card card-front" aria-label="Business card front">
    <span class="ghost-name" aria-hidden="true">KLV ROOFING</span>
    <div class="brand">
      <span class="brand-dot"></span>
      <span class="brand-name">KLV Roofing</span>
    </div>
  </section>

  <section class="card card-back" aria-label="Business card back">
    <span class="ghost-name" aria-hidden="true">KLV ROOFING</span>
    <div class="person">
      <p class="person-name">DANIEL REYES</p>
      <p class="person-role">Managing Director</p>
    </div>
    <p class="company">KLV Roofing</p>
    <div class="rule-main"></div>
    <ul class="contacts">
      <li>
        <svg viewBox="0 0 16 16" aria-hidden="true"><rect width="16" height="16" fill="#e4202a"/><path d="M5 3.5l2 2-1 1.2c.6 1.3 1.7 2.4 3 3l1.2-1 2 2-1.3 1.8C7.5 12.3 3.7 8.5 3.5 5z" fill="#fff"/></svg>
        (01) 4821 0376
      </li>
      <li>
        <svg viewBox="0 0 16 16" aria-hidden="true"><rect width="16" height="16" fill="#e4202a"/><rect x="5" y="3" width="6" height="10" rx="1" fill="#fff"/><rect x="6" y="4.5" width="4" height="6" fill="#e4202a"/></svg>
        (01) 4821 0377
      </li>
      <li>
        <svg viewBox="0 0 16 16" aria-hidden="true"><rect width="16" height="16" fill="#e4202a"/><rect x="3" y="4.5" width="10" height="7" fill="#fff"/><path d="M3 4.5l5 4 5-4" fill="none" stroke="#e4202a" stroke-width="1"/></svg>
        info@klvroofing.ca
      </li>
      <li>
        <svg viewBox="0 0 16 16" aria-hidden="true"><rect width="16" height="16" fill="#e4202a"/><circle cx="8" cy="8" r="4.5" fill="none" stroke="#fff" stroke-width="1.1"/><path d="M3.5 8h9M8 3.5c-2 2.5-2 6.5 0 9M8 3.5c2 2.5 2 6.5 0 9" fill="none" stroke="#fff" stroke-width="0.9"/></svg>
        www.klvroofing.ca
      </li>
    </ul>
    <div class="brand">
      <span class="brand-dot"></span>
      <span class="brand-name">KLV Roofing</span>
    </div>
    <div class="rule-address"></div>
    <p class="address">PO BOX 418 Maple Lane<br>7th street Brampton, ON</p>
  </section>
</main>
</body>
</html>
```